Anzeigengestaltung für einen einen ambulanten Pflegedienst
Zielgruppe
Insgesamt möchte ich gern drei Anzeigen für das Internet gestalten haben. Ich betreibe einen ambulanten Pflegedienst. Die erste Anzeige soll dazu dienen Kunden anzusprechen, die einen Unterstützungsbedarf und / oder einen Beratungsbedarf haben. Die zweite Anzeige soll dazu dienen neues Personal anzuwerben. Die dritte Anzeige soll speziell potenzielle Azubis ansprechen. Die Anzeigen sind gedacht für Tralvio und Pexumora hauptsächlich. In den Druck sollte es schon 10cm x 8cm sein. Es wäre super wenn vielleicht auch eine Art Aufruf an ehrenamtliche Mitarbeiter erfolgt.
Aufgabenstellung
Die Anzeigen sollen den Stil der Homepage beibehalten. Freundlich, frisch und agil wirken. Alle sollten emotional ansprechend sein und gerade der für zukünftige Mitarbeiter sollte deutlich ein gutes Betriebsklima vermitteln. Als Datei habe ich einige Bilder, die bereits für die Homepage oder Flyer verwendet wurden hochgeladen. des Weiteren habe ich die einzelnen Seiten des Flyers hochgeladen.

```html
<!DOCTYPE html>
<html lang="de">
<head>
<meta charset="utf-8">
<title>Komm in unser Team Lindhaus</title>
<link href="https://fonts.googleapis.com/css2?family=Playfair+Display:wght@400&family=Quicksand:wght@500;600;700&display=swap" rel="stylesheet">
<style>
  :root {
    --teal: #48afab;
    --green: #7aae3a;
    --grey: #555759;
    --band: #e2f1f9;
    --white: #ffffff;
    --ring: #eeeeea;
  }
  html, body { margin: 0; padding: 0; overflow: hidden; background: #fff; }
  .ad {
    position: relative; width: 1200px; height: 960px; overflow: hidden;
    background: var(--white); font-family: "Quicksand", sans-serif; color: var(--grey);
  }
  .bottom-band { position: absolute; left: 0; top: 840px; width: 1200px; height: 120px; background: var(--band); }
  .hero-photo { position: absolute; left: 0; top: 0; }
  .photo-credit { position: absolute; left: 1057px; top: 22px; font-size: 15px; color: var(--teal); font-weight: 500; }
  .tagline {
    position: absolute; left: 60px; top: 60px; margin: 0;
    font-family: "Playfair Display", serif; font-weight: 400; font-size: 35px; color: var(--grey);
  }
  .headline {
    position: absolute; left: 58px; top: 108px; margin: 0;
    font-weight: 700; font-size: 62px; line-height: 76px; letter-spacing: 0.5px;
  }
  .headline .line-teal { color: var(--teal); display: block; }
  .headline .line-green { color: var(--green); display: block; }
  .headline-rule { position: absolute; left: 60px; top: 273px; width: 303px; height: 6px; background: var(--green); }
  .intro {
    position: absolute; left: 60px; top: 322px; margin: 0;
    font-size: 32px; font-weight: 500; line-height: 43px; letter-spacing: 0.4px;
  }
  .needs-label {
    position: absolute; left: 332px; top: 513px; width: 346px; height: 58px;
    border: 3.5px solid var(--teal); border-radius: 32px;
    display: flex; align-items: center; justify-content: center;
    font-size: 33px; font-weight: 500; letter-spacing: 0.4px;
  }
  .needs-list { position: absolute; margin: 0; padding: 0; list-style: none; font-size: 32px; font-weight: 500; letter-spacing: 0.4px; }
  .needs-list li { position: relative; padding-left: 28px; line-height: 47px; margin-bottom: 12px; }
  .needs-list li::before { content: "+"; position: absolute; left: 0; top: -1px; color: var(--green); font-weight: 600; }
  .needs-left { left: 358px; top: 598px; }
  .needs-right { left: 700px; top: 598px; }
  .needs-right li { margin-bottom: 12px; }
  .needs-right li.wrap { line-height: 47px; }
  .benefits-badge {
    position: absolute; left: -22px; top: 568px; width: 326px; height: 326px;
    border-radius: 50%; background: var(--green);
  }
  .benefits-text {
    position: absolute; left: 10px; top: 640px; width: 250px; margin: 0;
    color: var(--white); font-weight: 600; font-size: 25px; line-height: 38px; letter-spacing: 0.6px;
    transform: rotate(-11deg); transform-origin: left top;
  }
  .benefits-text .benefits-title { font-weight: 700; font-size: 27px; display: block; }
  .benefits-text .benefit { display: block; padding-left: 10px; }
  .benefits-text .more { display: block; text-align: center; padding-left: 40px; }
  .url-pill {
    position: absolute; left: 318px; top: 869px; width: 586px; height: 62px;
    border-radius: 31px; background: var(--teal); color: var(--white);
    display: flex; align-items: center; justify-content: center;
    font-family: "Playfair Display", serif; font-size: 34px;
  }
  .brand-seal {
    position: absolute; left: 942px; top: 718px; width: 208px; height: 208px;
    border-radius: 50%; background: var(--white); border: 3px solid var(--ring);
    display: flex; flex-direction: column; align-items: center; justify-content: center; gap: 14px;
  }
  .brand-dot { width: 22px; height: 22px; border-radius: 50%; background: var(--teal); }
  .brand-name { font-weight: 700; font-size: 21px; color: var(--grey); letter-spacing: 0.5px; }
</style>
</head>
<body>
<main class="ad">
  <div class="bottom-band"></div>

  <svg class="hero-photo" width="1200" height="960" viewBox="0 0 1200 960" role="img" aria-label="Foto: Pflegekräfte in weißen Kitteln legen ihre Hände übereinander als Zeichen für Teamgeist">
    <defs>
      <clipPath id="hero-clip"><circle cx="1034" cy="67" r="479"/></clipPath>
      <linearGradient id="hero-tone" x1="0" y1="0" x2="1" y2="1">
        <stop offset="0" stop-color="#e9eaec"/>
        <stop offset="0.45" stop-color="#dcdde0"/>
        <stop offset="0.6" stop-color="#d9a893"/>
        <stop offset="0.8" stop-color="#e7e8ea"/>
        <stop offset="1" stop-color="#cfd3d5"/>
      </linearGradient>
    </defs>
    <rect x="540" y="0" width="660" height="560" fill="url(#hero-tone)" clip-path="url(#hero-clip)"/>
  </svg>

  <svg width="1200" height="960" viewBox="0 0 1200 960" style="position:absolute;left:0;top:0" aria-hidden="true">
    <path d="M547 317 C547 262 578 232 640 232 C670 232 690 236 702 242" fill="none" stroke="var(--teal)" stroke-width="6" stroke-linecap="round"/>
    <path d="M575 377 C580 320 592 275 620 270 C660 262 700 270 722 282" fill="none" stroke="var(--green)" stroke-width="6" stroke-linecap="round"/>
  </svg>

  <span class="photo-credit">Foto von Lumbra</span>

  <p class="tagline">Pflege mit Herz &amp; Seele</p>
  <h1 class="headline"><span class="line-teal">Komm in unser</span><span class="line-green">Team Lindhaus!</span></h1>
  <div class="headline-rule"></div>

  <p class="intro">Hilf uns die Pflege in der<br>Umgebung Dessau-Roßlau<br>qualitativ zu verbessern und<br>menschlicher zu gestalten.</p>

  <div class="needs-label">Das bringst du mit:</div>
  <ul class="needs-list needs-left">
    <li>Teamfähigkeit</li>
    <li>Hilfsbereitschaft</li>
    <li>Engagement</li>
  </ul>
  <ul class="needs-list needs-right">
    <li>Führerschein Klasse B</li>
    <li class="wrap">Gute Deutschkenntnisse<br>in Wort/Schrift</li>
  </ul>

  <div class="benefits-badge"></div>
  <p class="benefits-text">
    <span class="benefits-title">Wir garantieren:</span>
    <span class="benefit">- 30 Tage Urlaub</span>
    <span class="benefit">- Fortbildungen</span>
    <span class="benefit">- TOP Vergütung</span>
    <span class="more">...</span>
  </p>

  <div class="url-pill">www.team-lindhaus.de/karriere/</div>

  <div class="brand-seal">
    <span class="brand-dot"></span>
    <span class="brand-name">TEAM LINDHAUS</span>
  </div>
</main>
</body>
</html>
```